Velmora Cabinets Letter Head and Email Signature

Hi
I would love a design package for a letterhead, email signature, even update my business card if you like if you can come up with a great idea for my new high end cabinet shop. Velmora Cabinets brings timeless craftsmanship to modern interiors, specializing in high end, custom cabinetry designed for architects and interior designers.

Target Market(s)

high end, luxury market

Industry/Entity Type

cabinet making

Requirements
Must have
• my colours of logo as the theme

```html
<!DOCTYPE html>
<html lang="en">
<head>
<meta charset="utf-8">
<title>Velmora Cabinets – Letterhead and Email Signatures</title>
<link href="https://fonts.googleapis.com/css2?family=Poppins:wght@400;500;600&family=Arimo&family=Tinos&display=swap" rel="stylesheet">
<style>
  :root{
    --green:#4a7c3f;
    --ink:#111111;
    --text:#1e1e1e;
    --muted:#444444;
    --board:#d4d5d7;
    --panel:#9b9b9b;
    --paper:#ffffff;
  }
  *{margin:0;padding:0;box-sizing:border-box}
  html,body{width:1200px;height:829px;overflow:hidden;background:var(--board)}
  .board{position:relative;width:1200px;height:829px}

  /* letterhead */
  .letterhead{position:absolute;left:114px;top:117px;width:441px;height:624px;background:var(--paper);box-shadow:0 2px 10px rgba(0,0,0,.25);overflow:hidden}
  .brand{position:absolute;display:flex;align-items:center;gap:9px;font-family:'Poppins',sans-serif;font-weight:500;color:var(--green)}
  .brand-square{width:12px;height:12px;background:var(--green);flex:none}
  .letterhead .brand{left:26px;top:32px;font-size:24px;line-height:1.05}
  .letterhead .brand-square{width:16px;height:16px}
  .lh-contact{position:absolute;left:283px;top:23px;height:60px;border-left:1px solid var(--green);padding-left:8px;font-family:'Tinos',serif;font-size:8.6px;color:var(--muted);line-height:12px}
  .lh-contact li{list-style:none;display:flex;align-items:flex-start;gap:6px}
  .lh-contact svg{width:7px;height:7px;margin-top:2.5px;flex:none}
  .body-copy{position:absolute;left:67px;top:154px;width:310px;font-family:'Arimo',sans-serif;font-size:8.6px;line-height:9.9px;color:var(--text);text-align:justify}
  .body-copy p{margin-bottom:21px}
  .body-copy p.gap{margin-bottom:22px}
  .signature{position:absolute;left:67px;top:531px;width:150px;height:35px;background:linear-gradient(90deg,#eeeeee,#f7f7f7)}
  .wave{position:absolute;left:0;bottom:0;width:100%}

  /* email signatures */
  .sig-panel{position:absolute;width:462px;height:196px;background:var(--panel)}
  .sig-card{position:absolute;left:19px;top:24px;width:412px;height:138px;background:var(--paper);box-shadow:0 2px 6px rgba(0,0,0,.3);overflow:hidden;font-family:'Poppins',sans-serif}
  .sig-name{position:absolute;left:21px;font-size:17px;font-weight:600;color:var(--green);line-height:1}
  .sig-role{position:absolute;left:23px;font-size:9.5px;font-weight:500;color:var(--text);line-height:1}
  .sig-contacts{position:absolute;left:18px;list-style:none;font-size:11px;color:var(--text)}
  .sig-contacts li{display:flex;align-items:center;gap:6px}
  .dot{width:11px;height:11px;flex:none}
  .sig-card .brand{font-size:26px;line-height:1.05}
  .bar{position:absolute;left:0;bottom:0;width:100%;height:15px;display:flex;font-size:10.5px;color:#fff}
  .bar-address{flex:0 0 268px;background:var(--green);clip-path:polygon(0 0,100% 0,calc(100% - 7px) 100%,0 100%);display:flex;align-items:center;gap:7px;padding-left:10px}
  .bar-social{flex:1;background:var(--ink);margin-left:-5px;clip-path:polygon(7px 0,100% 0,100% 100%,0 100%);display:flex;align-items:center;justify-content:center;gap:3px;font-size:9.5px}
  .mini-square{width:5px;height:5px;background:#fff;display:inline-block}
  .handle{position:absolute;left:20px;bottom:6px;font-size:9.5px;color:#fff;display:flex;align-items:center;gap:3px}
</style>
</head>
<body>
<main class="board">

  <section class="letterhead" aria-label="Letterhead">
    <div class="brand"><span class="brand-square"></span><span>Velmora<br>Cabinets</span></div>
    <ul class="lh-contact">
      <li><svg viewBox="0 0 10 10"><path d="M2 1l2 2-1 1.2c.6 1.2 1.6 2.2 2.8 2.8L7 6l2 2-1.4 1.4C4.5 9 1 5.5.6 2.4z" fill="var(--green)"/></svg>0412558301</li>
      <li><svg viewBox="0 0 10 10"><rect x="0" y="2" width="10" height="7" fill="var(--green)"/><path d="M0 2l5 4 5-4" stroke="#fff" fill="none"/></svg>info@velmoracabinets.com.au</li>
      <li><svg viewBox="0 0 10 10"><circle cx="5" cy="5" r="4.5" fill="var(--green)"/><path d="M1 5h8M5 .5v9" stroke="#fff" stroke-width=".8"/></svg>www.websitename.com</li>
      <li><svg viewBox="0 0 10 10"><path d="M5 0a3.5 3.5 0 0 1 3.5 3.5C8.5 6 5 10 5 10S1.5 6 1.5 3.5A3.5 3.5 0 0 1 5 0z" fill="var(--green)"/><circle cx="5" cy="3.5" r="1.2" fill="#fff"/></svg>421, Address line here<br>Country Name, 45452</li>
    </ul>

    <div class="body-copy">
      <p>Lorem ipsum dolor sit amet, consectetur adipiscing elit. Donec fringilla neque euismod volutpat cursus. Vestibulum ac pretium orci, consequat elementum velit. Etiam bibendum purus ac augue finibus volutpat.</p>
      <p>Lorem ipsum dolor sit amet, consectetur adipiscing elit. Donec fringilla neque euismod volutpat cursus. Vestibulum ac pretium orci, consequat elementum velit. Etiam bibendum purus ac augue finibus volutpat.</p>
      <p>Lorem ipsum dolor sit amet, consectetur adipiscing elit. Donec fringilla neque euismod volutpat cursus. Vestibulum ac pretium orci, consequat elementum velit. Etiam bibendum purus ac augue finibus volutpat. Vestibulum justo nisl, gravida aliquet sollicitudin ut, finibus vitae mi. Praesent aliquet scelerisque blandit. Sed id varius lacus, id tristique sem. Fusce et lobortis leo. Aliquam mollis pellentesque magna, condimentum ullamcorper ex ullamcorper non. Morbi ultricies nunc eu tellus dignissim, eget venenatis dolor ullamcorper. Etiam dolor eros, iaculis at ultricies nec, volutpat nec orci.</p>
      <p>Lorem ipsum dolor sit amet, consectetur adipiscing elit. Donec fringilla neque euismod volutpat cursus. Vestibulum ac pretium orci, consequat elementum velit. Etiam bibendum purus ac augue finibus volutpat. Vestibulum justo nisl, gravida aliquet sollicitudin ut, finibus vitae mi. Praesent aliquet scelerisque blandit. Sed id varius lacus, id tristique sem. Fusce et lobortis leo. Aliquam mollis pellentesque magna, condimentum ullamcorper ex ullamcorper non. Morbi ultricies nunc eu tellus dignissim, eget venenatis dolor ullamcorper. Etiam dolor eros, iaculis at ultricies nec, volutpat nec orci.</p>
      <p>Lorem ipsum dolor sit amet, consectetur adipiscing elit. Donec fringilla neque euismod volutpat cursus. Vestibulum ac pretium orci, consequat elementum velit. Etiam bibendum purus ac augue finibus volutpat.</p>
    </div>

    <div class="signature" role="img" aria-label="Handwritten signature of the sender"></div>

    <svg class="wave" viewBox="0 0 441 40" height="40" preserveAspectRatio="none" aria-hidden="true">
      <path d="M0 19C80 8 200 12 300 22C370 29 410 30 441 22V40H0Z" fill="var(--ink)"/>
      <path d="M0 6C60 0 120 3 146 12C110 8 50 8 0 14Z" fill="var(--green)"/>
      <path d="M297 24C360 24 410 17 441 5V10C410 21 360 27 297 26Z" fill="var(--green)"/>
    </svg>
  </section>

  <section class="sig-panel" style="left:639px;top:199px" aria-label="Email signature, bar style">
    <div class="sig-card">
      <div class="sig-name" style="top:21px">Liam Thorsen</div>
      <div class="sig-role" style="top:38px">Director Craftsman</div>
      <ul class="sig-contacts" style="top:63px;line-height:15.2px">
        <li><svg class="dot" viewBox="0 0 10 10"><circle cx="5" cy="5" r="5" fill="var(--green)"/><path d="M3.3 2.3l1 1-.5.7c.3.6.8 1.1 1.4 1.4l.7-.5 1 1-.7.8C4.6 6.5 3 4.9 2.6 3z" fill="#fff"/></svg>0412558301</li>
        <li><svg class="dot" viewBox="0 0 10 10"><circle cx="5" cy="5" r="5" fill="var(--green)"/><rect x="2.5" y="3.2" width="5" height="3.6" fill="#fff"/><path d="M2.5 3.2L5 5.2l2.5-2" stroke="var(--green)" stroke-width=".6" fill="none"/></svg>info@velmoracabinets.com.au</li>
        <li><svg class="dot" viewBox="0 0 10 10"><circle cx="5" cy="5" r="5" fill="var(--green)"/><circle cx="5" cy="5" r="2.8" fill="none" stroke="#fff" stroke-width=".8"/><path d="M2.2 5h5.6" stroke="#fff" stroke-width=".7"/></svg>www.websitename.com</li>
      </ul>
      <div class="brand" style="left:212px;top:49px"><span class="brand-square"></span><span>Velmora<br>Cabinets</span></div>
      <div class="bar">
        <div class="bar-address"><svg width="7" height="9" viewBox="0 0 10 13"><path d="M5 0a4.5 4.5 0 0 1 4.5 4.5C9.5 8 5 13 5 13S.5 8 .5 4.5A4.5 4.5 0 0 1 5 0z" fill="#fff"/><circle cx="5" cy="4.5" r="1.6" fill="var(--green)"/></svg>421, Address line here Country Name, 45452</div>
        <div class="bar-social"><span class="mini-square"></span>@velmora.cabinets</div>
      </div>
    </div>
  </section>

  <section class="sig-panel" style="left:644px;top:437px" aria-label="Email signature, wave style">
    <div class="sig-card">
      <div class="sig-name" style="top:11px">Liam Thorsen</div>
      <div class="sig-role" style="top:29px">Director Craftsman</div>
      <ul class="sig-contacts" style="top:47px;line-height:12.8px">
        <li><svg class="dot" viewBox="0 0 10 10"><circle cx="5" cy="5" r="4.4" fill="none" stroke="var(--muted)" stroke-width="1"/><path d="M3.5 2.6l.9.9-.4.6c.3.5.7.9 1.2 1.2l.6-.4.9.9-.6.7C4.7 6.3 3.4 5 3.1 3.3z" fill="var(--muted)"/></svg>0412558301</li>
        <li><svg class="dot" viewBox="0 0 10 10"><circle cx="5" cy="5" r="4.4" fill="none" stroke="var(--muted)" stroke-width="1"/><rect x="3" y="3.6" width="4" height="2.8" fill="none" stroke="var(--muted)" stroke-width=".7"/></svg>info@velmoracabinets.com.au</li>
        <li><svg class="dot" viewBox="0 0 10 10"><circle cx="5" cy="5" r="4.4" fill="none" stroke="var(--muted)" stroke-width="1"/><circle cx="5" cy="5" r="2.3" fill="none" stroke="var(--muted)" stroke-width=".7"/></svg>www.websitename.com</li>
        <li style="margin-top:2px"><svg class="dot" viewBox="0 0 10 10"><circle cx="5" cy="5" r="4.4" fill="none" stroke="var(--muted)" stroke-width="1"/><path d="M5 2.4a1.7 1.7 0 0 1 1.7 1.7C6.7 5.4 5 7.6 5 7.6S3.3 5.4 3.3 4.1A1.7 1.7 0 0 1 5 2.4z" fill="var(--muted)"/></svg>421, Address line here Country Name, 45452</li>
      </ul>
      <div class="brand" style="left:282px;top:30px;flex-direction:column;align-items:flex-start;gap:6px"><span class="brand-square"></span><span>Velmora<br>Cabinets</span></div>
      <svg class="wave" viewBox="0 0 441 40" height="34" preserveAspectRatio="none" aria-hidden="true">
        <path d="M0 19C80 8 200 12 300 22C370 29 410 30 441 22V40H0Z" fill="var(--ink)"/>
        <path d="M0 6C60 0 120 3 146 12C110 8 50 8 0 14Z" fill="var(--green)"/>
        <path d="M297 24C360 24 410 17 441 5V10C410 21 360 27 297 26Z" fill="var(--green)"/>
      </svg>
      <div class="handle"><span class="mini-square"></span>@velmora.cabinets</div>
    </div>
  </section>

</main>
</body>
</html>
```